zAvora Corporate Website

zAvora is a well-funded start up developing an Online Marketing Platform for small businesses in Europe.
We are launching in February 2012 with all-in-one online marketing services including professional website, DIY SEO, Dashboard with Reports and Online marketing tools, and Support.
Our internal web designer has come up with a preliminary website design which we wish to continue to improve using new ideas, colours, layout, image, etc.
The brief is very simple - improve the website whether it is look & feel, ease of use, conversion rate - we are looking for overall improvements.
The contest will last 5 days and we will award the winner £300.
If you are the winner , you will also be required to provide designs for 3 more internal pages adhering to the proposed home page design.
Judging criteria : -
Visual Design
Layout must adhere to best practices and wire frame. If you decide to move elements around significantly please provide reason
Functional, informative and drives calls to action
Industry/Entity Type
Marketing
Look and feel
Each slider illustrates characteristics of the customer's brand and the style your logo design should communicate.

```html
<!DOCTYPE html>
<html lang="en">
<head>
<meta charset="utf-8">
<title>zAvora – Online Marketing Platform for Small Business</title>
<link href="https://fonts.googleapis.com/css2?family=Montserrat:wght@400;500;600&family=Arimo:wght@400;700&display=swap" rel="stylesheet">
<style>
:root{
  --sky:#5bc4e6;
  --ink:#2b2b2b;
  --text:#444a50;
  --night:#2b3038;
  --mist:#eff1f3;
  --rule:#d5d8dc;
  --muted:#9aa0a6;
  --white:#ffffff;
}
*{box-sizing:border-box;margin:0;padding:0}
html,body{width:899px;height:1200px;overflow:hidden}
body{position:relative;background:#f7f8f9;font-family:"Arimo",Arial,sans-serif;color:var(--text)}
.abs{position:absolute}
.heading{font-family:"Montserrat",Arial,sans-serif;color:var(--ink)}

.topbar{left:0;top:0;width:899px;height:58px;background:var(--mist);border-bottom:4px solid var(--sky)}
.search{left:691px;top:15px;width:189px;height:27px;background:var(--night);border:1px solid #111;border-radius:3px;color:#b7bcc2;font-size:11px;padding:6px 10px}
.search svg{position:absolute;right:9px;top:7px}

.stage{left:0;top:62px;width:899px;height:328px;background:var(--night)}
.navbar{left:19px;top:63px;width:861px;height:43px;background:linear-gradient(#a8afb9,#78818d);border-radius:0 0 3px 3px}
.brand{left:33px;top:71px;display:flex;align-items:center;gap:6px;font-family:"Montserrat",Arial,sans-serif;font-size:24px;font-weight:500;color:#3b4048}
.brand-dot{width:24px;height:24px;border-radius:50%;background:var(--sky)}
.nav{left:495px;top:72px;display:flex;font-family:"Montserrat",Arial,sans-serif;font-size:13.5px;font-weight:500;color:#24282e}
.nav a{color:inherit;text-decoration:none;height:27px;line-height:27px;padding:0 16px}
.nav a.active{background:var(--night);color:var(--white);border-radius:3px;padding:0 17px}

.band{left:0;top:390px;width:899px;height:90px;background:linear-gradient(#f5f6f7,#e6e8eb);box-shadow:0 2px 3px rgba(0,0,0,.12)}
.bubble{left:0;top:112px}
.hero{left:20px;top:118px;width:860px;height:292px;background:var(--white);border:4px solid var(--sky);border-radius:6px}
.hero-art{left:88px;top:170px;width:402px;height:238px;background:linear-gradient(135deg,#1c1f24 0%,#9fd3f0 8%,#d9effb 60%,#bfe3f6 100%);border-radius:8px 8px 0 0}
.hero-lines{left:585px;top:283px;font-family:"Montserrat",Arial,sans-serif;font-size:16.8px;line-height:27px;color:#4e545a;white-space:nowrap}
.hero-lines b{font-weight:400;color:var(--sky)}
.tagline{left:24px;top:436px;font-size:17.2px;font-weight:600;white-space:nowrap}
.offer{left:475px;top:431px;width:330px;font-family:"Montserrat",Arial,sans-serif;font-size:13px;line-height:18px;color:#2f3338}

.welcome-tab{left:0;top:507px;width:307px;height:29px;background:var(--sky);border-radius:0 3px 3px 0;padding:4px 0 0 28px;font-size:17px;font-weight:500}
.intro{left:24px;top:551px;width:850px;font-size:11px;line-height:16px}
.more{font-size:10px;color:var(--sky);font-weight:700;text-decoration:none}
.rule{left:19px;width:861px;height:1px;background:var(--rule)}

.services{left:18px;top:660px;width:862px;height:206px;display:flex}
.service{position:relative;flex:1;padding:0 6px 0 8px;border-left:1px solid var(--rule)}
.service:first-child{border-left:0;padding-left:0}
.service-head{display:flex;align-items:center;gap:6px;height:48px}
.icon{width:44px;height:44px;flex:none;border-radius:6px}
.service h3{font-size:12.5px;font-weight:600;line-height:16px;white-space:nowrap}
.service p{margin-top:6px;font-size:10.6px;line-height:16.2px;padding-left:8px}
.service .more{position:absolute;right:10px;bottom:8px;font-size:9px}

.col{top:893px;width:210px}
.col h2{font-size:16px;font-weight:500;padding:0 0 6px 8px;white-space:nowrap}
.underline{display:block;margin-bottom:8px}
.col a.link{display:block;color:var(--sky);font-family:"Montserrat",Arial,sans-serif;font-size:10.8px;line-height:16px;font-weight:500;text-decoration:none}
.col p{font-family:"Montserrat",Arial,sans-serif;font-size:10.6px;line-height:16px;color:#33383d}
.col .meta{font-size:8.5px;color:var(--muted);margin:2px 0 10px}
.col .who{color:var(--sky);font-weight:500}
.btn{top:1045px;height:22px;padding:0 9px;background:linear-gradient(#8d9298,#676c72);border-radius:3px;color:var(--white);font-family:"Montserrat",Arial,sans-serif;font-size:10.5px;line-height:22px;white-space:nowrap}
.btn::after{content:"";position:absolute;left:10px;bottom:-6px;border-left:6px solid #676c72;border-bottom:6px solid transparent}

.awards{left:695px;top:884px;width:185px;height:198px;background:var(--sky);border-radius:3px}
.awards-card{left:718px;top:887px;width:138px;height:192px;background:var(--white);padding:14px 0 0 16px;font-size:8.5px;color:#555}
.badge{width:100px;height:72px;background:linear-gradient(#dfe4ea,#b9c3cf);margin-bottom:4px}
.badge.second{height:52px;margin-top:14px;background:linear-gradient(#e8eaec,#c7ccd1)}

.footer{left:0;top:1101px;width:899px;height:99px;background:var(--night)}
.foot-nav{left:272px;top:1127px;display:flex;gap:28px;font-size:11px;color:#d8dbdf}
.foot-nav span.sep{color:#9aa0a6}
.copy{left:352px;top:1155px;font-size:10.5px;color:#c4c8cc}
.top-link{left:790px;top:1112px;display:flex;align-items:center;gap:4px;font-size:11px;font-weight:700;color:var(--white)}
.social{left:750px;top:1146px;display:flex;gap:6px}
.social span{width:20px;height:20px;border-radius:2px}
</style>
</head>
<body>

<header>
  <div class="abs topbar"></div>
  <div class="abs search">Search...
    <svg width="11" height="11" viewBox="0 0 11 11"><circle cx="4.5" cy="4.5" r="3.4" fill="none" stroke="#c9ced3" stroke-width="1.5"/><line x1="7" y1="7" x2="10" y2="10" stroke="#c9ced3" stroke-width="1.6"/></svg>
  </div>
  <div class="abs stage"></div>
  <div class="abs navbar"></div>
  <div class="abs brand"><span class="brand-dot"></span>zAvora</div>
  <nav class="abs nav">
    <a class="active" href="#">Home</a><a href="#">Products</a><a href="#">About Us</a><a href="#">Contact Us</a>
  </nav>
</header>

<section class="hero-area">
  <div class="abs band"></div>
  <svg class="abs bubble" width="899" height="330" viewBox="0 0 899 330">
    <path d="M14 10 H885 V300 H858 L832 328 L840 300 H14 Z" fill="#1c2026"/>
  </svg>
  <div class="abs hero"></div>
  <div class="abs hero-art" role="img" aria-label="Laptop showing a marketing dashboard with gauges and a rising line chart"></div>
  <p class="abs hero-lines">We set up everything in <b>3 hours</b><br>You manage it-<b>15 mins</b> per week<br>We provide <b>full support</b></p>
  <h1 class="abs heading tagline">Online Marketing Platform for Small Business</h1>
  <p class="abs offer">Get a big business website and sales tools from £19/month. It's Easy, Powerful and Low Cost.</p>
</section>

<section class="welcome">
  <h2 class="abs heading welcome-tab">Welcome to our site</h2>
  <p class="abs intro">Sed ut perspiciatis unde omnis iste natus error sit voluptatem accusantium doloremque laudantium, totam rem aperiam, eaque ipsa quae ab illo inventore veritatis et quasi architecto beatae vitae dicta sunt explicabo. Nemo enim ipsam voluptatem quia voluptas sit aspernatur aut odit aut fugit, sed quia consequuntur magni dolores eos qui ratione voluptatem sequi nesciunt. Neque porro quisquam est, qui dolorem ipsum quia dolor sit amet, consectetur, adipisci velit, sed quia non numquam eius modi tempora incidunt ut labore et dolore magnam aliquam quaerat voluptatem.</p>
  <a class="abs more" style="left:818px;top:628px" href="#">Read more</a>
  <div class="abs rule" style="top:647px"></div>
</section>

<section class="abs services">
  <article class="service">
    <div class="service-head"><span class="icon" role="img" aria-label="Globe icon" style="background:radial-gradient(circle at 35% 35%,#8fd0f5,#1f6fb8);border-radius:50%"></span><h3 class="heading">Website Design<br>and Development</h3></div>
    <p>Neque porro quisquam est, qui dolorem ipsum quia dolor sit amet, consectetur, adipisci velit, sed quia non numquam eius modi tempora incidunt ut labore et dolore magnam aliquam quaerat voluptatem.</p>
    <a class="more" href="#">+ Find more</a>
  </article>
  <article class="service">
    <div class="service-head"><svg class="icon" viewBox="0 0 44 44" role="img" aria-label="Bar chart icon"><rect x="2" y="6" width="11" height="36" fill="#5cb82e"/><rect x="16" y="22" width="11" height="20" fill="#d9312b"/><rect x="30" y="14" width="11" height="28" fill="#f2a31b"/></svg><h3 class="heading">Strategy and<br>Analysis</h3></div>
    <p>Neque porro quisquam est, qui dolorem ipsum quia dolor sit amet, consectetur, adipisci velit, sed quia non numquam eius modi tempora incidunt ut labore et dolore magnam aliquam quaerat voluptatem.</p>
    <a class="more" href="#">+ Find more</a>
  </article>
  <article class="service">
    <div class="service-head"><svg class="icon" viewBox="0 0 44 44" role="img" aria-label="Magnifier icon"><circle cx="17" cy="17" r="13" fill="#eef3f7" stroke="#9aa3ab" stroke-width="3"/><line x1="27" y1="27" x2="41" y2="41" stroke="#555b61" stroke-width="5" stroke-linecap="round"/></svg><h3 class="heading">Online Marketing</h3></div>
    <p>Neque porro quisquam est, qui dolorem ipsum quia dolor sit amet, consectetur, adipisci velit, sed quia non numquam eius modi tempora incidunt ut labore et dolore magnam aliquam quaerat voluptatem.</p>
    <a class="more" href="#">+ Find more</a>
  </article>
  <article class="service">
    <div class="service-head"><svg class="icon" viewBox="0 0 44 44" role="img" aria-label="Phone icon"><rect x="10" y="1" width="24" height="42" rx="4" fill="#1b1d20"/><rect x="12" y="6" width="20" height="30" fill="#3a3f45"/></svg><h3 class="heading">Interactive<br>Technology</h3></div>
    <p>Neque porro quisquam est, qui dolorem ipsum quia dolor sit amet, consectetur, adipisci velit, sed quia non numquam eius modi tempora incidunt ut labore et dolore magnam aliquam quaerat voluptatem.</p>
    <a class="more" href="#">+ Find more</a>
  </article>
  <article class="service">
    <div class="service-head"><span class="icon" role="img" aria-label="Feed icon" style="background:linear-gradient(#f77a2b,#d9500f)"></span><h3 class="heading">E-Learning</h3></div>
    <p>Neque porro quisquam est, qui dolorem ipsum quia dolor sit amet, consectetur, adipisci velit, sed quia non numquam eius modi tempora incidunt ut labore et dolore magnam aliquam quaerat voluptatem.</p>
    <a class="more" href="#">+ Find more</a>
  </article>
</section>
<div class="abs rule" style="top:874px"></div>

<section class="news">
  <div class="abs col" style="left:20px">
    <h2 class="heading">What ‘ve done recently</h2>
    <svg class="underline" width="200" height="8"><path d="M0 1 H16 L22 7 L28 1 H200" fill="none" stroke="#c5c9cd"/></svg>
    <a class="link" href="#">Lorem Ipsum is simply dummy.</a>
    <p>Neque porro quisquam est, qui dolorem ipsum quia dolor sit amet, consectetur, adipisci velit, sed quia non numquam eius modi tempora incidunt ut labore et dolore magnam aliquam quaerat voluptatem.</p>
  </div>
  <div class="abs btn" style="left:18px">Visit our blog</div>

  <div class="abs col" style="left:247px">
    <h2 class="heading">From the blog</h2>
    <svg class="underline" width="172" height="8"><path d="M0 1 H16 L22 7 L28 1 H172" fill="none" stroke="#c5c9cd"/></svg>
    <a class="link" href="#">Lorem Ipsum is simply dummy text of the printing and typesetting industry.</a>
    <p class="meta">Posted by marta,17 August</p>
    <a class="link" href="#">Lorem Ipsum is simply dummy text of the printing and typesetting industry.</a>
    <p class="meta">Posted by marta,17 August</p>
  </div>
  <div class="abs btn" style="left:245px">Visit our blog</div>

  <div class="abs col" style="left:475px">
    <h2 class="heading">Latest posts</h2>
    <svg class="underline" width="172" height="8"><path d="M0 1 H16 L22 7 L28 1 H172" fill="none" stroke="#c5c9cd"/></svg>
    <p>Lorem Ipsum is simply dummy text of the printing and typesetting industry.<br><span class="who">Daniel Reeves</span>, <span style="color:var(--muted);font-size:8.5px">5days ago</span></p>
    <p style="margin-top:10px">Lorem Ipsum is simply dummy text of the printing and typesetting industry.<br><span class="who">Daniel Reeves</span>, <span style="color:var(--muted);font-size:8.5px">5days ago</span></p>
  </div>
  <div class="abs btn" style="left:474px">Follow us on Chirper</div>

  <aside class="abs awards"></aside>
  <div class="abs awards-card">
    <div class="badge" role="img" aria-label="Growth listing badge"></div>
    <p>2004, 2005, 2007, 2008</p>
    <div class="badge second" role="img" aria-label="Business awards badge"></div>
    <p>Finalist<br>2004, 2005, 2006, 2009, 2010</p>
  </div>
</section>

<footer>
  <div class="abs footer"></div>
  <div class="abs top-link">Return to top
    <svg width="16" height="16" viewBox="0 0 16 16"><path d="M8 1 L15 8 H11 V15 H5 V8 H1 Z" fill="#7cc531"/></svg>
  </div>
  <nav class="abs foot-nav"><span>Home</span><span class="sep">|</span><span>Products</span><span class="sep">|</span><span>About Us</span><span class="sep">|</span><span>Contact Us</span></nav>
  <p class="abs copy">© Copyrights 2012.All rights receved</p>
  <div class="abs social">
    <span style="background:#3b5a98"></span><span style="background:#4fb6e8"></span><span style="background:#f06a23"></span><span style="background:#1f7bb6"></span><span style="background:#e0e0e0"></span>
  </div>
</footer>

</body>
</html>
```